IT Consultant specialising in Quince support and repairs needs new business card design

Looking for modern clean card design with new logo element for IT business. Specialising in Quince products so looking for a design/logo element that will be immediately recognisable. Would also like social media icons to convey alternate communication avenues are available. VistaNook, Quibbler, WorkNexo as well as traditional Address, Phone, Email and Website.
Target Market(s)
Local Area Consumer and Business clientele
Industry/Entity Type
Communication
Contact Information for Business Card
Dorian Welk
Director
0498272046
dorian@orbitandnoderepairs.com.au
5/27 Marlowend Place, Burleigh Heads QLD 4220
Logo Text
Orbit and Node Repairs
Requirements
Must have
- Small icon elements where required and Quibbler, Vistanook, Work Nexo icons just so people recognise there are other methods of communication.
- Back side of card to have space to write name, number and details with light shade lines
Nice to have
- clean bright look with colour

```html
<!DOCTYPE html>
<html lang="en">
<head>
<meta charset="utf-8">
<title>Orbit and Node Repairs – Business Card</title>
<link href="https://fonts.googleapis.com/css2?family=Oswald:wght@500;600&family=Open+Sans:wght@400;600&display=swap" rel="stylesheet">
<style>
  :root {
    --bg: #e9e6e1;
    --card-dark: #1f2021;
    --card-dark-2: #2b2c2e;
    --panel: #2f3032;
    --paper: #fbfbfb;
    --paper-shade: #e9e9e9;
    --green: #8fd13a;
    --ink: #3a3b3d;
    --light-text: #e8e8e8;
    --icon-bg: #cfd0d1;
    --social-a: #3d7fb5;
    --social-b: #5fb3e0;
  }
  * { box-sizing: border-box; margin: 0; padding: 0; }
  html, body { width: 1200px; height: 1000px; overflow: hidden; background: var(--bg); }
  body { position: relative; font-family: "Open Sans", sans-serif; }

  .card {
    position: absolute;
    left: 220px;
    width: 760px;
    height: 434px;
    border-radius: 6px;
    overflow: hidden;
    box-shadow: 0 10px 28px rgba(0,0,0,.18);
  }

  /* ---------- Front ---------- */
  .card-front { top: 50px; background: var(--card-dark); }
  .front-paper {
    position: absolute; left: 0; top: 0; width: 100%; height: 258px;
    background: linear-gradient(135deg, var(--paper) 40%, var(--paper-shade));
  }
  .front-rule {
    position: absolute; left: 0; top: 258px; width: 100%; height: 9px;
    background: var(--green);
  }
  .front-band {
    position: absolute; left: 0; top: 267px; width: 100%; height: 167px;
    background: linear-gradient(180deg, var(--card-dark-2), var(--card-dark));
  }
  .brand {
    position: absolute; left: 52px; top: 150px;
    display: flex; align-items: center; gap: 14px;
  }
  .brand-mark { width: 34px; height: 34px; background: var(--green); }
  .brand-name {
    font-weight: 600; font-size: 34px; color: var(--ink); letter-spacing: -0.5px;
  }
  .contacts {
    position: absolute; left: 52px; top: 292px;
    list-style: none; display: flex; flex-direction: column; gap: 9px;
  }
  .contact {
    display: flex; align-items: center; gap: 12px;
    color: var(--light-text); font-size: 17px; white-space: nowrap;
  }
  .contact-icon {
    width: 22px; height: 22px; border-radius: 3px; flex: none;
    background: var(--icon-bg); display: flex; align-items: center; justify-content: center;
  }
  .contact-icon svg { width: 15px; height: 15px; }

  /* ---------- Back ---------- */
  .card-back { top: 516px; background: linear-gradient(160deg, var(--card-dark-2), var(--card-dark)); }
  .name-panel {
    position: absolute; right: 0; top: 0; width: 300px; height: 230px;
    background: var(--panel);
  }
  .back-bar { position: absolute; height: 14px; background: var(--green); box-shadow: 0 0 10px rgba(143,209,58,.45); }
  .back-bar-top { left: 0; top: 58px; width: 460px; }
  .back-bar-low { right: 0; top: 168px; width: 150px; }
  .person { position: absolute; right: 38px; top: 88px; text-align: right; }
  .person-name {
    font-family: "Oswald", sans-serif; font-weight: 600; font-size: 40px;
    letter-spacing: 1px; color: #ffffff; line-height: 1;
  }
  .person-name .surname { color: var(--green); }
  .person-role {
    font-size: 16px; letter-spacing: 2px; color: var(--light-text); margin-top: 4px;
  }
  .socials {
    position: absolute; left: 52px; bottom: 46px;
    list-style: none; display: flex; flex-direction: column; gap: 10px;
  }
  .social {
    display: flex; align-items: center; gap: 12px;
    color: var(--light-text); font-size: 16px; letter-spacing: 1px;
  }
  .social-square { width: 22px; height: 22px; border-radius: 3px; background: var(--social-a); }
  .social-square.alt { background: var(--social-b); }
</style>
</head>
<body>

<section class="card card-front" aria-label="Card front">
  <div class="front-paper"></div>
  <div class="brand">
    <span class="brand-mark" aria-hidden="true"></span>
    <span class="brand-name">Orbit and Node Repairs</span>
  </div>
  <div class="front-rule"></div>
  <div class="front-band"></div>
  <ul class="contacts">
    <li class="contact">
      <span class="contact-icon"><svg viewBox="0 0 16 16"><path d="M4 1.5h3l1 3.5-2 1.2c.8 1.8 2.2 3.2 4 4l1.2-2 3.5 1v3c0 .9-.7 1.5-1.5 1.5C6.8 13.7 2.3 9.2 2.5 3 2.5 2.2 3.1 1.5 4 1.5z" fill="#2b2c2e"/></svg></span>
      0498272046
    </li>
    <li class="contact">
      <span class="contact-icon"><svg viewBox="0 0 16 16" fill="none" stroke="#2b2c2e" stroke-width="1.4"><circle cx="8" cy="8" r="6.2"/><ellipse cx="8" cy="8" rx="2.6" ry="6.2"/><path d="M1.8 8h12.4"/></svg></span>
      www.orbitandnoderepairs.com.au
    </li>
    <li class="contact">
      <span class="contact-icon"><svg viewBox="0 0 16 16" fill="none" stroke="#2b2c2e" stroke-width="1.4"><rect x="1.5" y="3.5" width="13" height="9"/><path d="M1.5 3.5 8 9l6.5-5.5"/></svg></span>
      dorian@orbitandnoderepairs.com.au
    </li>
    <li class="contact">
      <span class="contact-icon"><svg viewBox="0 0 16 16"><path d="M8 1.8 1.5 7.5h2v6.5h3.5v-4h2v4h3.5V7.5h2z" fill="#2b2c2e"/></svg></span>
      5/27 Marlowend Place, Tallowmere Bay QLD 4296
    </li>
  </ul>
</section>

<section class="card card-back" aria-label="Card back">
  <div class="name-panel"></div>
  <div class="back-bar back-bar-top"></div>
  <div class="back-bar back-bar-low"></div>
  <div class="person">
    <div class="person-name">DORIAN <span class="surname">WELK</span></div>
    <div class="person-role">DIRECTOR</div>
  </div>
  <ul class="socials">
    <li class="social"><span class="social-square"></span>YOUR VISTANOOK</li>
    <li class="social"><span class="social-square alt"></span>YOUR QUIBBLER</li>
    <li class="social"><span class="social-square"></span>YOUR WORKNEXO</li>
  </ul>
</section>

</body>
</html>
```